Namibia currently imports 60% of its food. Harvest Crest Oruva is an initiative which will assist Namibia to become self sustainable in terms of food production. We aim to do this through the development of 3 agricultural production zones which will include farming zones, local farmer assistance, processing and distribution of the final products. Please see our project overview attached.

```html
<!DOCTYPE html>
<html lang="en">
<head>
<meta charset="utf-8">
<title>Harvest Crest Oruva</title>
<link rel="stylesheet" href="https://fonts.googleapis.com/css2?family=Cinzel:wght@400;500&family=Montserrat:wght@400;500;600;700;800&display=swap">
<style>
:root{
  --green:#0e6b38;
  --green-deep:#0b5a2f;
  --forest:#2a3d1e;
  --tan:#c4a07b;
  --sky:#6fc5e9;
  --cream:#f6f0e8;
  --ink:#1b1b1b;
  --text:#555;
  --white:#fff;
}
*{margin:0;padding:0;box-sizing:border-box}
html,body{width:1200px;height:3256px;overflow:hidden;background:var(--white)}
body{font-family:"Montserrat",sans-serif;color:var(--text);position:relative}
.page{position:relative;width:1200px;height:3256px;overflow:hidden}
.abs{position:absolute}
.btn{position:absolute;display:flex;align-items:center;justify-content:center;background:var(--tan);color:var(--white);font-weight:700;font-size:15px;border-radius:30px;letter-spacing:.3px}
.heading{font-family:"Cinzel",serif;font-weight:400;color:var(--green);line-height:1.05}
.body-copy{font-size:15.3px;line-height:24px;text-align:justify}

/* header */
.site-header{position:absolute;left:0;top:0;width:1200px;height:97px;background:var(--white);z-index:3}
.brand{position:absolute;left:143px;top:32px;font-family:"Cinzel",serif;font-size:23px;color:var(--green);letter-spacing:.5px;display:flex;align-items:center;gap:10px}
.brand-dot{width:12px;height:12px;border-radius:50%;background:var(--green)}
.nav{position:absolute;top:38px;font-size:14.6px;font-weight:500;color:#222}
.search{position:absolute;left:1022px;top:31px;width:32px;height:32px;border-radius:50%;background:var(--green)}

/* hero */
.hero{position:absolute;left:0;top:97px;width:1200px;height:600px;background:linear-gradient(180deg,#7d8a8f 0%,#6b7a5c 25%,#4f6b3a 55%,#5c6f3b 80%,#6b7a3f 100%)}
.hero-title{position:absolute;left:0;top:228px;width:1200px;text-align:center;color:var(--white);font-weight:800;font-size:46px;line-height:54px;z-index:2}
.slider-arrow{position:absolute;width:34px;height:34px;border-radius:50%;background:var(--white);border:3px solid var(--green);z-index:2}

/* photo circles */
.photo{position:absolute;border-radius:50%}
.photo::before{content:"";position:absolute;inset:-13px;border-radius:50%;border:4px solid transparent;border-left-color:var(--green);border-bottom-color:var(--green);transform:rotate(10deg)}

/* zones */
.zones{position:absolute;left:0;top:1125px;width:1200px;height:721px;background:linear-gradient(180deg,var(--cream) 0%,#efe9df 38%,#b9c4a0 48%,#6f9a3e 58%,#4c7d2a 80%,#3f6d24 100%)}
.zone{position:absolute;width:298px;height:298px;border-radius:50%;display:flex;flex-direction:column;align-items:center;color:var(--white);font-weight:600;font-size:23.5px;line-height:32px;text-align:center;padding-top:50px}
.zone svg{margin-bottom:28px}
.zone-ring{position:absolute;width:328px;height:328px;border-radius:50%;border:3px solid var(--white)}

/* processing */
.processing{position:absolute;left:0;top:1846px;width:1200px;height:520px;background:var(--forest)}

/* contact */
.field{position:absolute;background:var(--white);border:1px solid #bbb;font-size:10px;color:#555;padding:6px 10px}
.info-icon{position:absolute;left:784px;width:34px;height:34px;border-radius:50%;border:2px solid var(--white)}
.info-text{position:absolute;left:836px;color:var(--white);font-size:12.5px;line-height:17px}
.social{position:absolute;top:3091px;width:26px;height:26px;border-radius:50%}
</style>
</head>
<body>
<div class="page">

<header class="site-header">
  <div class="brand"><span>HARVEST CREST ORUVA</span><span class="brand-dot"></span></div>
  <span class="nav" style="left:540px">HOME</span>
  <span class="nav" style="left:614px">ABOUT US</span>
  <span class="nav" style="left:720px">SERVICES</span>
  <span class="nav" style="left:821px">NEWS</span>
  <span class="nav" style="left:895px">CONTACT US</span>
  <div class="search"><svg width="32" height="32" viewBox="0 0 32 32"><circle cx="14.5" cy="14.5" r="4.5" fill="none" stroke="#fff" stroke-width="2"/><line x1="18" y1="18" x2="21" y2="21" stroke="#fff" stroke-width="2.2" stroke-linecap="round"/></svg></div>
</header>

<section class="hero" role="img" aria-label="Landscape photo of mountains above a river with rapids and green bushland"></section>
<h1 class="hero-title abs" style="top:227px">AN KTV AGRI-TECH, FOOD<br>SECURITY INITIATIVE</h1>
<div class="btn" style="left:523px;top:363px;width:154px;height:56px;z-index:2">GET STARTED</div>
<svg class="abs" style="left:0;top:440px;z-index:1" width="1200" height="260" viewBox="0 0 1200 260">
  <path d="M0,22 C150,80 300,140 430,175 C560,210 700,232 830,225 C1010,215 1140,130 1200,30 L1200,260 L0,260 Z" fill="#fff"/>
  <path d="M420,172 C560,212 700,232 830,225 C1010,215 1140,130 1200,30" fill="none" stroke="var(--green)" stroke-width="11"/>
</svg>
<div class="slider-arrow" style="left:348px;top:562px"><svg width="28" height="28" viewBox="0 0 28 28"><path d="M18,14 H10 M13,10 L9,14 L13,18" fill="none" stroke="#222" stroke-width="2"/></svg></div>
<div class="slider-arrow" style="left:385px;top:575px"><svg width="28" height="28" viewBox="0 0 28 28"><path d="M10,14 H18 M15,10 L19,14 L15,18" fill="none" stroke="#222" stroke-width="2"/></svg></div>

<!-- about -->
<h2 class="heading abs" style="left:166px;top:700px;font-size:52px">About Us</h2>
<p class="body-copy abs" style="left:166px;top:768px;width:420px">Namibia is a young democracy in Sub-Saharan Africa with a population of approximately 2.5 Million people. The country’s agricultural sector has been slow to keep up with the increasing population. As a consequence, approximately 60% of the food required to feed the nation is imported. The elevated cost of these imported foods means a large proportion of the population consume food with low nutritional value. Despite vast tracts of available arable land and abundant water resources</p>
<div class="btn" style="left:166px;top:1009px;width:155px;height:57px">READ MORE</div>
<div class="photo" style="left:667px;top:702px;width:366px;height:366px;background:radial-gradient(circle at 40% 35%,#9fb7c9 0%,#7a8f6a 45%,#6b4a35 80%,#4d3426 100%)" role="img" aria-label="Farm workers loading sweet potatoes into crates beside a tractor"></div>

<!-- zones -->
<section class="zones" role="img" aria-label="Green crop field under a pale sky"></section>
<svg class="abs" style="left:0;top:1125px" width="1200" height="240" viewBox="0 0 1200 240">
  <path d="M0,0 L1200,0 L1200,215 C1000,150 750,80 560,45 C360,10 150,30 0,210 Z" fill="#fff"/>
  <path d="M0,210 C150,30 360,10 560,45 C680,66 800,95 860,112" fill="none" stroke="var(--green)" stroke-width="11"/>
</svg>
<h2 class="heading abs" style="left:0;top:1250px;width:1200px;text-align:center;font-size:48px;line-height:55px">OUR<br>PRODUCTION ZONES</h2>
<div class="zone-ring" style="left:148px;top:1423px"></div>
<div class="zone-ring" style="left:434px;top:1423px"></div>
<div class="zone-ring" style="left:721px;top:1423px"></div>
<div class="zone" style="left:163px;top:1438px;background:var(--green)">
  <svg width="86" height="86" viewBox="0 0 86 86" fill="none" stroke="#fff" stroke-width="3"><rect x="30" y="8" width="26" height="16"/><path d="M10,30 H76 M16,30 L6,80 M32,30 L28,80 M54,30 L58,80 M70,30 L80,80"/></svg>
  FARMING<br>ZONES</div>
<div class="zone" style="left:449px;top:1438px;background:var(--sky)">
  <svg width="86" height="86" viewBox="0 0 86 86" fill="none" stroke="#fff" stroke-width="3"><path d="M60,80 V30 M60,46 C50,40 46,30 48,22 C56,26 60,36 60,46 M60,38 C70,32 74,22 72,14 C64,18 60,28 60,38 M20,80 H80"/></svg>
  LOCAL FARMER<br>ASSISTANCE</div>
<div class="zone" style="left:736px;top:1438px;background:var(--tan)">
  <svg width="86" height="86" viewBox="0 0 86 86" fill="none" stroke="#fff" stroke-width="3"><rect x="10" y="40" width="26" height="30"/><rect x="40" y="50" width="26" height="20"/><path d="M66,56 H76 L80,64 V70 H66"/><circle cx="48" cy="74" r="4"/><circle cx="72" cy="74" r="4"/><rect x="20" y="12" width="24" height="20"/></svg>
  PROCESSING AND<br>DISTRIBUTION</div>

<!-- processing -->
<section class="processing"></section>
<h2 class="heading abs" style="left:143px;top:1896px;font-size:55px;line-height:54px;color:var(--white)">Processing<br>Facilities</h2>
<p class="body-copy abs" style="left:521px;top:1895px;width:534px;color:var(--white)">Each of the allocated production zones will be furnished with handling, processing and milling facilities for all crops produced as part of the program. These will include Potatoes, Maize and Wheat. Harvest Crest Oruva will undertake primary production of the food goods and market them into the Namibian food supply chain.</p>
<div class="btn" style="left:521px;top:2041px;width:155px;height:57px">READ MORE</div>

<svg class="abs" style="left:0;top:2120px" width="1200" height="260" viewBox="0 0 1200 260">
  <path d="M0,226 C300,100 600,25 860,20 C1030,18 1150,130 1200,215 L1200,260 L0,260 Z" fill="#fff"/>
  <path d="M560,58 C680,32 780,20 860,20 C1030,18 1150,130 1200,215" fill="none" stroke="var(--green)" stroke-width="12"/>
</svg>

<!-- education -->
<h2 class="heading abs" style="left:582px;top:2262px;font-size:55px;line-height:54px">HARVEST CREST<br>EDUCATION</h2>
<p class="body-copy abs" style="left:582px;top:2388px;width:420px">Give a man a fish and feed him for a day, teach a man to fish and feed him for a lifetime” Education is key to empowerment and we embrace that concept. As such, we aim to offer a vocational education scheme for the participants in the Harvest Crest Oruva program. We aim to furnish the participants with the skills to be successful and sustainable farmers in their own rights.</p>
<div class="btn" style="left:582px;top:2581px;width:155px;height:57px">READ MORE</div>
<div class="photo" style="left:158px;top:2314px;width:366px;height:366px;background:radial-gradient(circle at 55% 40%,#e8e6e0 0%,#9dbb6a 35%,#4f7f2d 70%,#2f5a1f 100%)" role="img" aria-label="Young farmer using a tablet in a maize field"></div>

<!-- contact -->
<svg class="abs" style="left:0;top:2660px" width="1200" height="596" viewBox="0 0 1200 596">
  <path d="M0,230 C300,110 600,30 850,22 C1020,18 1150,100 1200,166 L1200,596 L0,596 Z" fill="var(--ink)"/>
  <path d="M560,52 C680,30 780,14 850,12 C1020,8 1150,80 1200,140" fill="none" stroke="var(--green)" stroke-width="11"/>
</svg>
<h2 class="heading abs" style="left:0;top:2796px;width:1200px;text-align:center;font-size:52px">Contact</h2>
<div class="abs" style="left:169px;top:2892px;color:var(--white);font-size:16px;font-weight:500">GET IN TOUCH:</div>
<div class="field" style="left:172px;top:2932px;width:265px;height:28px">NAME :</div>
<div class="field" style="left:448px;top:2932px;width:265px;height:28px">PHONE :</div>
<div class="field" style="left:172px;top:2973px;width:541px;height:28px">EMAIL :</div>
<div class="field" style="left:172px;top:3013px;width:541px;height:66px">MESSAGE :</div>
<div class="btn" style="left:635px;top:3099px;width:78px;height:28px;font-size:11px">SUBMIT</div>

<div class="abs" style="left:784px;top:2892px;color:var(--white);font-size:16px;font-weight:500">CONTACT INFORMATION</div>
<div class="info-icon" style="top:2934px"><svg width="30" height="30" viewBox="0 0 30 30"><path d="M15,22 C11,17 10,15 10,13 A5,5 0 0 1 20,13 C20,15 19,17 15,22 Z" fill="none" stroke="#fff" stroke-width="1.8"/><circle cx="15" cy="13" r="1.8" fill="#fff"/></svg></div>
<div class="info-text" style="top:2933px">123,Excepteur sint occaecat cupi<br>datat non proiden</div>
<div class="info-icon" style="top:2982px"><svg width="30" height="30" viewBox="0 0 30 30"><path d="M10,9 L13,9 L14,13 L12,14 C13,16 14,17 16,18 L17,16 L21,17 L21,20 C15,21 9,15 10,9 Z" fill="#fff"/></svg></div>
<div class="info-text" style="top:2991px">+1 888 888 8888</div>
<div class="info-icon" style="top:3025px"><svg width="30" height="30" viewBox="0 0 30 30"><rect x="8" y="10" width="14" height="10" fill="#fff"/><path d="M8,10 L15,16 L22,10" fill="none" stroke="var(--ink)" stroke-width="1.4"/></svg></div>
<div class="info-text" style="top:3034px">hello@harvestcrest.example</div>
<div class="social" style="left:786px;background:var(--green)"></div>
<div class="social" style="left:820px;background:var(--tan)"></div>
<div class="social" style="left:854px;background:var(--green)"></div>
<div class="social" style="left:889px;background:var(--tan)"></div>

<div class="abs" style="left:133px;top:3176px;width:935px;height:1px;background:#444"></div>
<div class="abs" style="left:0;top:3211px;width:1200px;text-align:center;color:var(--white);font-size:12.5px">Copyrights © 2024, HCO. All Rights Reserved.&nbsp; | &nbsp;Privacy policy</div>

</div>
</body>
</html>
```